Tusk Hollow Lodge website (design only)

Tusk Hollow Lodge (http://www.tuskhollowlodge-mw.example) is a private Safari lodge located in Malawi.
We would like a modern, professional website designed that does not subscribe to the cliched view of a Safari in Africa, but still maintain a wildlife/safari atmosphere.

The aim of our website is to entice people & drive them to the booking form.

Here are some examples of websites that we like. Although we would like our site to be a bit more in line with modern web design trends.

http://www.marulaplains.example/
http://www.kovunde.example/
http://www.tembalorecamp.example/

Requirements
Must have
• Here is a list of the pages required. Most of them will follow a standard content layout. I.e. heading, body and images.

If you take a look at the website, you will get an idea of hoe many page types there are +- 5

http://www.tuskhollowlodge-mw.example/index.htm

About Tusk Hollow
Lirundu Country Club
Rooms
Conferences
Cuisine
Facilities
Your Safari
Activities
Rates & Special Offers
Booking form
Latest Developments
How To Get There
Gallery
Contact Us
Blog / Newsfeed

```html
<!DOCTYPE html>
<html lang="en">
<head>
<meta charset="utf-8">
<title>Tusk Hollow Lodge</title>
<link href="https://fonts.googleapis.com/css2?family=Jost:wght@400;500&family=Parisienne&display=swap" rel="stylesheet">
<style>
:root{
  --page:#2e2926;
  --panel:#7b7358;
  --nav:#8b846a;
  --nav-active:#a7a087;
  --nav-text:#2a2520;
  --gold:#d3bd82;
  --link:#c9ae6b;
  --body-text:#b4ab94;
  --rule:#6e6650;
  --tagline:#b9ae93;
  --footer:#746d55;
  --footer-text:#2a2520;
}
*{margin:0;padding:0;box-sizing:border-box}
html,body{width:1200px;height:901px;overflow:hidden;background:var(--page);font-family:Arial,Helvetica,sans-serif}
.page{position:relative;width:1200px;height:901px}
.brand{position:absolute;left:52px;top:30px}
.brand-name{font-family:'Jost',sans-serif;font-weight:400;font-size:44px;color:var(--tagline);letter-spacing:1px;line-height:1}
.brand-place{margin-top:12px;margin-left:66px;font-size:12px;letter-spacing:1px;color:var(--tagline)}
.tagline{position:absolute;right:52px;top:44px;font-family:'Parisienne',cursive;font-size:30px;color:var(--tagline)}
.showcase{position:absolute;left:54px;top:129px;width:1096px;height:502px;background:var(--panel)}
.main-nav{display:flex;height:32px;background:var(--nav);align-items:center;font-size:13.5px;color:var(--nav-text)}
.main-nav a{color:inherit;text-decoration:none;padding:0 13px;height:32px;line-height:32px;position:relative}
.main-nav a+a::before{content:"|";position:absolute;left:-3px;color:#5d5744}
.main-nav a.active{background:var(--nav-active);padding:0 17px}
.main-nav{justify-content:space-between}
.hero{position:absolute;left:8px;top:34px;width:1079px;height:363px;
  background:linear-gradient(180deg,#6e5a3c 0%,#c97a2a 30%,#e58b1c 45%,#1a140e 58%,#120d08 66%,#b9661c 78%,#d88a2a 86%,#1a120a 100%)}
.thumbs{position:absolute;left:0;top:411px;width:100%;height:79px}
.thumb{position:absolute;top:0;width:140px;height:79px;border:1px solid #f3efe4}
.arrow{position:absolute;top:32px;color:#e9e3d2;font-size:13px}
.features{position:absolute;left:0;top:648px;width:1200px}
.feature{position:absolute;top:0}
.feature h2{font-family:'Jost',sans-serif;font-weight:500;font-size:15px;letter-spacing:.3px;color:var(--gold);text-align:center;border-top:1px solid var(--rule);border-bottom:1px solid var(--rule);height:46px;line-height:44px}
.feature p{margin-top:14px;padding:0 3px;font-size:12.6px;line-height:16.4px;color:var(--body-text)}
.feature .links{font-size:12.6px;color:var(--link);padding:0 3px}
.feature .links span{color:var(--body-text);margin:0 8px}
.divider{position:absolute;top:649px;width:1px;height:168px;background:#463f35}
.site-footer{position:absolute;left:0;top:870px;width:1200px;height:31px;background:var(--footer)}
.social{position:absolute;left:52px;top:0;display:flex;height:31px;align-items:center}
.social span{display:flex;align-items:center;justify-content:center;width:46px;height:31px;border-left:1px solid #625b47}
.social span:last-child{border-right:1px solid #625b47}
.footer-links{position:absolute;left:323px;top:0;line-height:31px;font-size:13px;color:var(--footer-text)}
.footer-links i{font-style:normal;margin:0 6px}
</style>
</head>
<body>
<div class="page">
  <header>
    <div class="brand">
      <div class="brand-name">Tusk Hollow Lodge</div>
      <div class="brand-place">NKHOMBA ESTATE &nbsp;|&nbsp; MTENJE</div>
    </div>
    <div class="tagline">Experience the endless beauty of Nature</div>
  </header>

  <section class="showcase">
    <nav class="main-nav">
      <a class="active">Home</a><a>About</a><a>Lirundu Country Club</a><a>Safari</a><a>Lodge</a><a>Activities</a><a>Rates &amp; Specials</a><a>Bookings</a><a>Developments</a><a>Directions</a><a>Contact</a>
    </nav>
    <div class="hero" role="img" aria-label="Sunset over a still lake with silhouetted trees reflected in the water"></div>
    <div class="thumbs">
      <span class="arrow" style="left:10px">&lsaquo;</span>
      <div class="thumb" role="img" aria-label="Zebra grazing" style="left:33px;background:linear-gradient(#6f8a3e,#b8b39b)"></div>
      <div class="thumb" role="img" aria-label="Impala in the bush" style="left:181px;background:linear-gradient(#5f7a35,#b58a5c)"></div>
      <div class="thumb" role="img" aria-label="Antelope in green grass" style="left:329px;background:linear-gradient(#3f5a2a,#7fa94a)"></div>
      <div class="thumb" role="img" aria-label="Giraffe among foliage" style="left:477px;background:linear-gradient(#4d6d2a,#c7a26a)"></div>
      <div class="thumb" role="img" aria-label="Antelope resting on sand" style="left:625px;background:linear-gradient(#c49a73,#a7764f)"></div>
      <div class="thumb" role="img" aria-label="Sable antelope" style="left:773px;background:linear-gradient(#6fa04a,#6d5a40)"></div>
      <div class="thumb" role="img" aria-label="Wildebeest grazing" style="left:921px;background:linear-gradient(#8fbf5a,#5d6a45)"></div>
      <span class="arrow" style="right:10px">&rsaquo;</span>
    </div>
  </section>

  <section class="features">
    <article class="feature" style="left:58px;width:229px">
      <h2>TUSK HOLLOW LODGE</h2>
      <p>Warmest welcome to the unique Malawi experience: lodge complex, game park, the 18 hole Lirundu golf club &amp; Lusanje dam. Tusk Hollow Lodge provides all the holiday and business prerequisites in a beautiful, relaxing environment.</p>
      <div class="links">Read more...</div>
    </article>
    <article class="feature" style="left:351px;width:214px">
      <h2>LIRUNDU COUNTRY CLUB</h2>
      <p>Lorem ipsum dolor sit amet, consect etuer adipiscing elit, sed diam nonum my nibh euismod tincidunt ut laoreet dolore magna aliquam erat volutpat. Ut wisi enim ad minim veniam quis no strud exerci tatin ullamcorper suscipit</p>
      <div class="links">Read more<span>|</span>Booking Enquiry</div>
    </article>
    <article class="feature" style="left:630px;width:221px">
      <h2>THE LODGE &amp; ROOMS</h2>
      <p>Lorem ipsum dolor sit amet, consect etuer adipiscing elit, sed diam nonum my nibh euismod tincidunt ut laoreet dolore magna aliquam erat volutpat. Ut wisi enim ad minim veniam quis no strud exerci tatin ullamcorper suscipit</p>
      <div class="links">Read more<span>|</span>Booking Enquiry</div>
    </article>
    <article class="feature" style="left:919px;width:224px">
      <h2>CONFERENCE &amp; RESTURANT</h2>
      <p>Lorem ipsum dolor sit amet, consect etuer adipiscing elit, sed diam nonum my nibh euismod tincidunt ut laoreet dolore magna aliquam erat volutpat. Ut wisi enim ad minim veniam quis no strud exerci tatin ullamcorper suscipit</p>
      <div class="links">Read more<span>|</span>Booking Enquiry</div>
    </article>
  </section>
  <div class="divider" style="left:318px"></div>
  <div class="divider" style="left:599px"></div>
  <div class="divider" style="left:884px"></div>

  <footer class="site-footer">
    <div class="social">
      <span><svg width="12" height="12"><rect width="12" height="12" fill="#4a4434"/></svg></span>
      <span><svg width="12" height="12"><rect width="12" height="12" fill="#4a4434"/></svg></span>
      <span><svg width="16" height="12" viewBox="0 0 16 12"><rect x="0.5" y="0.5" width="15" height="11" fill="none" stroke="#4a4434"/><path d="M0.5 0.5 L8 7 L15.5 0.5" fill="none" stroke="#4a4434"/></svg></span>
    </div>
    <div class="footer-links">Tusk Hollow Lodge copyright &copy; 2012<i>|</i>Privacy Policy<i>|</i>Blog<i>|</i>Contact<i>|</i>Booking Enquiries</div>
  </footer>
</div>
</body>
</html>
```